Velvet Dice Night Age Verification Landing Page

To create a visually appealing design for the landing page of the adult game "Velvet Dice Night" that confirms the visitor's age.
The design should have a simple and visually appealing look that focuses on two buttons labeled "Yes" and "No". The purpose of the page is to confirm that the visitor is 18 years of age or older before accessing the game's content. Responsive design that works well on desktop and mobile devices. The final output should be delivered in PSD, AI, or Sketch format, along with any necessary images or assets.
I have also attached examples.

```html
<!DOCTYPE html>
<html lang="en">
<head>
<meta charset="UTF-8">
<title>Velvet Dice Night — Age Verification</title>
<link href="https://fonts.googleapis.com/css2?family=Poppins:wght@500;600&display=swap" rel="stylesheet">
<style>
  :root {
    --accent: #9b5cb5;
    --accent-light: #a868c2;
    --panel: rgba(20, 16, 20, 0.86);
    --text: #ffffff;
    --scene-dark: #1e1c26;
    --scene-warm: #6b4a3c;
    --scene-floor: #4e535c;
  }
  * { box-sizing: border-box; margin: 0; padding: 0; }
  html, body {
    width: 1200px;
    height: 857px;
    overflow: hidden;
    font-family: "Poppins", sans-serif;
    color: var(--text);
    background: var(--scene-dark);
  }
  .page {
    position: relative;
    width: 1200px;
    height: 857px;
    overflow: hidden;
  }
  .backdrop-photo {
    position: absolute;
    inset: 0;
    background:
      radial-gradient(ellipse 420px 300px at 560px 420px, rgba(150, 100, 80, 0.55), transparent 70%),
      radial-gradient(ellipse 300px 240px at 960px 300px, rgba(150, 110, 110, 0.35), transparent 70%),
      linear-gradient(180deg, #2b2a38 0%, #3a2e34 35%, var(--scene-warm) 58%, #5a5558 74%, var(--scene-floor) 100%);
  }
  .age-gate {
    position: absolute;
    left: 337px;
    top: 189px;
    width: 526px;
    height: 480px;
    background: var(--panel);
    display: flex;
    flex-direction: column;
    align-items: center;
  }
  .brand {
    margin-top: 140px;
    display: flex;
    align-items: center;
    gap: 12px;
  }
  .brand-dot {
    width: 18px;
    height: 18px;
    border-radius: 50%;
    background: var(--accent-light);
  }
  .brand-name {
    font-weight: 600;
    font-size: 34px;
    color: var(--accent-light);
    letter-spacing: 0.3px;
  }
  .age-question {
    margin-top: 68px;
    font-weight: 500;
    font-size: 21px;
    line-height: 1;
  }
  .answer-row {
    margin-top: 14px;
    display: flex;
    gap: 16px;
  }
  .answer-btn {
    width: 86px;
    height: 51px;
    border: none;
    background: var(--accent);
    color: var(--text);
    font-family: "Poppins", sans-serif;
    font-weight: 500;
    font-size: 19px;
  }
  .remember {
    margin-top: 19px;
    display: flex;
    align-items: center;
    gap: 7px;
    font-weight: 500;
    font-size: 16px;
  }
  .remember-box {
    width: 13px;
    height: 13px;
    background: var(--text);
    border-radius: 2px;
  }
</style>
</head>
<body>
  <main class="page">
    <div class="backdrop-photo" role="img" aria-label="Softly lit photo of a couple embracing on a bed with blurred bokeh lights behind, hands clasped in the foreground"></div>

    <section class="age-gate">
      <div class="brand">
        <span class="brand-dot"></span>
        <span class="brand-name">Velvet Dice Night</span>
      </div>
      <p class="age-question">Are you over 18 years of age?</p>
      <div class="answer-row">
        <button class="answer-btn">Yes</button>
        <button class="answer-btn">No</button>
      </div>
      <label class="remember">
        <span class="remember-box"></span>
        Remember me
      </label>
    </section>
  </main>
</body>
</html>
```